Harbourline Electrical Solutions

On one side. LOGO (underneath:) Commercial Industrial Residential

- NAME & CONTACT DETAILS

Marcus T. Hollings
Project Manager

(Cell icon) (441) 555-0187
(Email icon) hlelectricalsolutions@mailvento.com
(Facebook & Instagram icons )@hlelectricalsolutions

Other side: LOGO - underneath ELECTRICAL CONSTRUCTION & MAINTENANCE . LED LIGHTING & AUTOMATION . LIFE SAFETY SYSTEMS (FIRE ALARM / SECURITY) . DATA & COMMUNICATION

```html
<!DOCTYPE html>
<html lang="en">
<head>
<meta charset="utf-8">
<title>Harbourline Electrical Solutions – Business Card</title>
<link rel="stylesheet" href="https://fonts.googleapis.com/css2?family=Montserrat:wght@500;600;700&family=Open+Sans:wght@400;500&display=swap">
<style>
  :root {
    --backdrop: #a6a6a6;
    --card-white: #ffffff;
    --brand-teal: #0e5366;
    --pattern-teal: #15607a;
    --ink-dark: #333333;
    --ink-mid: #555555;
    --on-teal: #ffffff;
  }
  * { margin: 0; padding: 0; box-sizing: border-box; }
  html, body {
    width: 1200px; height: 1055px; overflow: hidden;
    background: var(--backdrop);
  }
  .stage { position: relative; width: 1200px; height: 1055px; }
  .card {
    position: absolute; top: 182px; width: 375px; height: 657px;
  }
  .card--front { left: 181px; background: var(--card-white); }
  .card--back { left: 647px; background: var(--brand-teal); overflow: hidden; }

  .brand {
    position: absolute; top: 52px; left: 0; width: 100%;
    display: flex; align-items: center; justify-content: center; gap: 10px;
  }
  .brand__square { width: 14px; height: 14px; background: var(--brand-teal); }
  .brand__name {
    font-family: "Montserrat", sans-serif; font-weight: 700;
    font-size: 17px; letter-spacing: 0.5px; color: var(--brand-teal);
    text-transform: uppercase; line-height: 1.15; text-align: left;
  }
  .sectors {
    position: absolute; top: 113px; width: 100%; text-align: center;
    font-family: "Montserrat", sans-serif; font-weight: 500;
    font-size: 11.5px; letter-spacing: 0.3px; color: var(--ink-dark);
  }
  .sectors .dot { margin: 0 4px; }

  .person { position: absolute; top: 424px; width: 100%; text-align: center; }
  .person__name {
    font-family: "Montserrat", sans-serif; font-weight: 700;
    font-size: 22px; letter-spacing: 0.6px; color: var(--brand-teal);
    text-transform: uppercase;
  }
  .person__role {
    font-family: "Open Sans", sans-serif; font-weight: 500;
    font-size: 15px; color: var(--ink-dark); margin-top: 3px;
  }
  .contact-icons {
    position: absolute; top: 490px; width: 100%;
    display: flex; justify-content: center; gap: 7px;
  }
  .contact-icons svg { width: 26px; height: 26px; }
  .contact {
    position: absolute; top: 541px; width: 100%; text-align: center;
    font-family: "Open Sans", sans-serif; font-size: 14px;
    line-height: 20.5px; color: var(--ink-mid);
  }

  .back-pattern {
    position: absolute; inset: 0;
    background: linear-gradient(180deg, var(--pattern-teal), var(--brand-teal));
  }
  .services {
    position: absolute; top: 494px; left: 38px; list-style: none;
    font-family: "Open Sans", sans-serif; font-size: 14px;
    line-height: 18.5px; color: var(--on-teal);
  }
  .services li { position: relative; padding-left: 16px; }
  .services li::before {
    content: ""; position: absolute; left: 0; top: 6px;
    width: 7px; height: 7px; border-radius: 50%; background: var(--on-teal);
  }
</style>
</head>
<body>
<main class="stage">
  <section class="card card--front">
    <div class="brand">
      <span class="brand__square"></span>
      <span class="brand__name">Harbourline<br>Electrical Solutions</span>
    </div>
    <p class="sectors">COMMERCIAL<span class="dot">•</span>INDUSTRIAL<span class="dot">•</span>RESIDENTIAL</p>

    <div class="person">
      <h1 class="person__name">Marcus T. Hollings</h1>
      <p class="person__role">Project Manager</p>
    </div>

    <div class="contact-icons">
      <svg viewBox="0 0 26 26" aria-label="Phone">
        <circle cx="13" cy="13" r="12" fill="none" stroke="var(--brand-teal)" stroke-width="1.2"/>
        <rect x="9.5" y="6.5" width="7" height="13" rx="1.2" fill="none" stroke="var(--brand-teal)" stroke-width="1.4"/>
        <line x1="12" y1="17.3" x2="14" y2="17.3" stroke="var(--brand-teal)" stroke-width="1.2"/>
      </svg>
      <svg viewBox="0 0 26 26" aria-label="Email">
        <circle cx="13" cy="13" r="12" fill="none" stroke="var(--brand-teal)" stroke-width="1.2"/>
        <rect x="7.5" y="9" width="11" height="8" rx="1" fill="var(--brand-teal)"/>
        <polyline points="7.8,9.5 13,13.5 18.2,9.5" fill="none" stroke="#fff" stroke-width="1"/>
      </svg>
      <svg viewBox="0 0 26 26" aria-label="Social profile">
        <circle cx="13" cy="13" r="12" fill="none" stroke="var(--brand-teal)" stroke-width="1.2"/>
        <circle cx="13" cy="13" r="6" fill="var(--brand-teal)"/>
      </svg>
      <svg viewBox="0 0 26 26" aria-label="Social profile">
        <circle cx="13" cy="13" r="12" fill="none" stroke="var(--brand-teal)" stroke-width="1.2"/>
        <circle cx="13" cy="13" r="6" fill="var(--brand-teal)"/>
      </svg>
    </div>

    <p class="contact">
      (441) 555-0187<br>
      hlelectricalsolutions@mailvento.com<br>
      @hlelectricalsolutions
    </p>
  </section>

  <section class="card card--back">
    <div class="back-pattern" role="img" aria-label="Tone-on-tone repeating brand monogram pattern in teal"></div>
    <ul class="services">
      <li>Electrical Construction &amp; Maintenance</li>
      <li>LED Lighting &amp; Automation</li>
      <li>Life Safety Systems(Fire Alarm / Security)</li>
      <li>Data &amp; Communication</li>
    </ul>
  </section>
</main>
</body>
</html>
```